Locksmith Business Cards

My father-in-law is in need of new business cards for his locksmith business and I need to impress him. Kindly help me out!

You can see the previous business card attached. It is a family run business in North Wales.

No individual names on the cards.

Key Things to Feature:
- The words "Prompt", "Local", "Reliable" (as you can see under the logo on the website)
- 24h Emergency Service
- Covering All of North Wales, the Wirral and Chester
- The color blue
- A key or a lock would be interesting (similar to the ones that come up when you google locksmith business card)

Optional (only if design includes bullet points, like the example below):
https://imgvaultcdn.net/samples/208314/55172/55172_3904821_208314_image.jpg
- Residential / Commercial / Automotive
- Alarms & Cameras
- Key Cutting & Safes

https://www.brynhafod-locksmiths.co.uk/

Industry/Entity Type

Locksmith

Contact Information for Business Card

01632 960 418
07700 900 362
brynhafodlocksmiths@mailvane.com
Brynhafod Locksmiths, The Willow Barn, 7 Tannery Rd., Llandudno LL99 4QX
www.brynhafod-locksmiths.co.uk

Requirements
Must have
• - The words "Prompt", "Local", "Reliable" (as you can see under the logo on the website)
• - 24h Emergency Service
• - Covering All of North Wales, the Wirral and Chester
Nice to have
• - A key or a lock would be interesting (similar to the ones that come up when you google locksmith business card)

```html
<!DOCTYPE html>
<html lang="en">
<head>
<meta charset="utf-8">
<title>Brynhafod Locksmiths – Business Cards</title>
<link href="https://fonts.googleapis.com/css2?family=Oswald:wght@500&family=Exo+2:wght@400;500&family=Montserrat:wght@500&display=swap" rel="stylesheet">
<style>
  :root {
    --backdrop: #1b1b1d;
    --navy: #1f2670;
    --navy-deep: #1a2060;
    --band: #4052a0;
    --accent: #1e9be0;
    --ink: #ffffff;
    --ink-soft: #dfe3f5;
  }
  * { margin: 0; padding: 0; box-sizing: border-box; }
  html, body {
    width: 1200px; height: 1050px; overflow: hidden;
    background: var(--backdrop);
  }
  .sheet {
    position: relative; width: 1200px; height: 1050px;
    display: flex; flex-direction: column; align-items: center;
    justify-content: center; gap: 70px;
  }
  .card {
    position: relative; width: 700px; height: 400px;
    border-radius: 22px; overflow: hidden;
    background: linear-gradient(135deg, var(--navy) 0%, var(--navy-deep) 100%);
    color: var(--ink);
  }

  /* Brand lockup */
  .brand { display: flex; align-items: center; gap: 18px; }
  .brand-mark {
    width: 22px; height: 22px; border-radius: 50%;
    background: var(--ink); flex-shrink: 0;
  }
  .brand-name {
    font-family: "Oswald", sans-serif; font-weight: 500;
    text-transform: uppercase; line-height: 0.95; color: var(--ink);
  }
  .tagline {
    font-family: "Montserrat", sans-serif; font-weight: 500;
    text-transform: uppercase; letter-spacing: 0.14em; color: var(--ink-soft);
    display: flex; gap: 14px;
  }
  .tagline .divider { opacity: 0.8; }

  /* Front */
  .card-front .brand {
    position: absolute; left: 165px; top: 125px;
  }
  .card-front .brand-name { font-size: 56px; letter-spacing: 0.01em; }
  .card-front .tagline {
    position: absolute; left: 205px; top: 270px; font-size: 17px;
  }

  /* Back */
  .card-back .brand { position: absolute; left: 150px; top: 50px; }
  .card-back .brand-name { font-size: 46px; }
  .services {
    position: absolute; left: 395px; top: 160px; list-style: none;
    font-family: "Exo 2", sans-serif; font-size: 15px; line-height: 1.38;
  }
  .services li { position: relative; padding-left: 22px; }
  .services li::before {
    content: ""; position: absolute; left: 0; top: 8px;
    width: 6px; height: 6px; border-radius: 50%; background: var(--accent);
  }
  .contacts {
    position: absolute; left: 40px; top: 205px; list-style: none;
    font-family: "Exo 2", sans-serif; font-size: 15px; line-height: 1.32;
  }
  .contacts li { display: flex; align-items: flex-start; gap: 12px; }
  .contacts svg { width: 14px; height: 14px; margin-top: 3px; flex-shrink: 0; fill: var(--accent); }
  .contacts .address-line { padding-left: 26px; }
  .footer-band {
    position: absolute; left: 0; right: 0; bottom: 0; height: 90px;
    background: var(--band);
    clip-path: polygon(0 55%, 100% 0, 100% 100%, 0 100%);
  }
  .card-back .tagline {
    position: absolute; right: 40px; bottom: 28px; font-size: 14px;
  }
</style>
</head>
<body>
<main class="sheet">

  <section class="card card-front" aria-label="Business card front">
    <div class="brand">
      <span class="brand-mark"></span>
      <div class="brand-name">Brynhafod<br>Locksmiths</div>
    </div>
    <p class="tagline"><span>Prompt</span><span class="divider">|</span><span>Local</span><span class="divider">|</span><span>Reliable</span></p>
  </section>

  <section class="card card-back" aria-label="Business card back">
    <div class="brand">
      <span class="brand-mark"></span>
      <div class="brand-name">Brynhafod<br>Locksmiths</div>
    </div>

    <ul class="services">
      <li>24h Emergency Service</li>
      <li>Covering All of North Wales,<br>the Wirral and Chester</li>
      <li>Residential / Commercial / Automotive</li>
      <li>Alarms &amp; Cameras</li>
      <li>Key Cutting &amp; Safes</li>
    </ul>

    <ul class="contacts">
      <li><svg viewBox="0 0 16 16"><path d="M3 1h3l1 4-2 1a9 9 0 0 0 5 5l1-2 4 1v3a2 2 0 0 1-2 2A13 13 0 0 1 1 3a2 2 0 0 1 2-2z"/></svg>01632 960 418</li>
      <li><svg viewBox="0 0 16 16"><path d="M3 1h3l1 4-2 1a9 9 0 0 0 5 5l1-2 4 1v3a2 2 0 0 1-2 2A13 13 0 0 1 1 3a2 2 0 0 1 2-2z"/></svg>07700 900 362</li>
      <li><svg viewBox="0 0 16 16"><path d="M1 3h14v10H1z M1 3l7 6 7-6" fill="none" stroke="#1e9be0" stroke-width="1.6"/></svg>brynhafodlocksmiths@mailvane.com</li>
      <li><svg viewBox="0 0 16 16"><circle cx="8" cy="8" r="6.5" fill="none" stroke="#1e9be0" stroke-width="1.5"/><path d="M1.5 8h13M8 1.5c-3 3.5-3 9.5 0 13M8 1.5c3 3.5 3 9.5 0 13" fill="none" stroke="#1e9be0" stroke-width="1.2"/></svg>www.brynhafod-locksmiths.co.uk</li>
      <li><svg viewBox="0 0 16 16"><path d="M8 1a5 5 0 0 1 5 5c0 4-5 9-5 9S3 10 3 6a5 5 0 0 1 5-5zm0 3a2 2 0 1 0 0 4 2 2 0 0 0 0-4z"/></svg>The Willow Barn, 7 Tannery Rd.,</li>
      <li class="address-line">Llandudno LL99 4QX</li>
    </ul>

    <div class="footer-band"></div>
    <p class="tagline"><span>Prompt</span><span class="divider">|</span><span>Local</span><span class="divider">|</span><span>Reliable</span></p>
  </section>

</main>
</body>
</html>
```